Home Security Company Business Card

Looking for a eye catching business card that is non traditional and stands out but yet still looks professional. It should include all the pertinent information such as name, title, address, telephone, e-mail, website address should definitely stand out and then finally the logo.

Target Market(s)

Residential and Commercial accounts mostly upscale accounts

Industry/Entity Type

Security

Contact Information for Business Card

Name
Title
Address
Office #
Cell #
E-mail
Website

Font styles to use
Serif
Sans Serif

Requirements
Must have
• Logo, two sided color configuration
Nice to have
• You decide
Should not have
• There really aren't any.

```html
<!DOCTYPE html>
<html lang="en">
<head>
<meta charset="utf-8">
<title>Hartwell Security Systems Inc. – Business Card</title>
<link rel="stylesheet" href="https://fonts.googleapis.com/css2?family=Crimson+Text:wght@400;600&family=Source+Sans+3:wght@400&display=swap">
<style>
  :root {
    --brand-red: #7a1416;
    --brand-gold: #e7ae3a;
    --card-white: #ffffff;
    --backdrop: #efe4d2;
    --social-1: #4a66a8;
    --social-2: #3a9fdc;
    --social-3: #1f6ba3;
    --serif: "Crimson Text", Georgia, serif;
    --sans: "Source Sans 3", Arial, sans-serif;
  }
  html, body {
    margin: 0;
    padding: 0;
    width: 1189px;
    height: 1200px;
    overflow: hidden;
    background: var(--backdrop);
  }
  .card {
    position: absolute;
    left: 171px;
    width: 856px;
    height: 487px;
    border-radius: 22px;
    box-shadow: 0 6px 14px rgba(0,0,0,0.25);
    overflow: hidden;
  }
  .card-front { top: 68px; background: var(--brand-red); }
  .card-back { top: 626px; background: var(--card-white); }

  .front-wordmark {
    position: absolute;
    left: 0; right: 0;
    top: 178px;
    text-align: center;
    color: var(--card-white);
    font-family: var(--serif);
    font-weight: 600;
    line-height: 1;
  }
  .front-wordmark .name { display: block; font-size: 96px; letter-spacing: 1px; }
  .front-wordmark .sub { display: block; font-size: 49px; margin-top: 2px; letter-spacing: -0.5px; }

  .back-mark {
    position: absolute;
    left: 60px; top: 86px;
    width: 84px; height: 84px;
    background: var(--brand-gold);
  }
  .back-wordmark {
    position: absolute;
    left: 175px; top: 78px;
    color: var(--brand-red);
    font-family: var(--serif);
    font-weight: 600;
    line-height: 1;
  }
  .back-wordmark .name { display: block; font-size: 63px; }
  .back-wordmark .sub { display: block; font-size: 30px; margin-top: 2px; letter-spacing: -0.4px; }

  .social { position: absolute; top: 86px; width: 35px; height: 35px; }
  .social-1 { left: 659px; background: var(--social-1); }
  .social-2 { left: 713px; background: var(--social-2); }
  .social-3 { left: 767px; background: var(--social-3); }

  .holder { position: absolute; right: 54px; top: 236px; text-align: right; }
  .holder-name { font-family: var(--sans); font-size: 37px; color: var(--brand-red); line-height: 1; }
  .holder-title { font-family: var(--sans); font-size: 23px; color: var(--brand-gold); line-height: 1; margin-top: 2px; letter-spacing: 1px; }
  .rule { position: absolute; left: 49px; width: 665px; top: 280px; height: 2px; background: var(--brand-gold); }

  .contacts { position: absolute; left: 53px; top: 352px; margin: 0; padding: 0; list-style: none; }
  .contacts li {
    display: flex; align-items: center;
    height: 30px;
    font-family: var(--serif); font-size: 24px; color: var(--brand-red);
  }
  .contacts svg { width: 23px; height: 23px; margin-right: 15px; flex: none; }

  .address {
    position: absolute; right: 54px; top: 348px;
    text-align: right; font-family: var(--serif); font-size: 24px; color: var(--brand-red);
    line-height: 28px;
  }
  .address .web { color: var(--brand-gold); display: block; margin-top: 7px; letter-spacing: 0.5px; }
</style>
</head>
<body>
  <section class="card card-front" aria-label="Card front">
    <div class="front-wordmark">
      <span class="name">HARTWELL</span>
      <span class="sub">SECURITY SYSTEMS INC.</span>
    </div>
  </section>

  <section class="card card-back" aria-label="Card back">
    <div class="back-mark" aria-hidden="true"></div>
    <div class="back-wordmark">
      <span class="name">HARTWELL</span>
      <span class="sub">SECURITY SYSTEMS INC.</span>
    </div>

    <span class="social social-1" aria-label="Social profile"></span>
    <span class="social social-2" aria-label="Social profile"></span>
    <span class="social social-3" aria-label="Social profile"></span>

    <div class="holder">
      <div class="holder-name">Marcus Bell</div>
      <div class="holder-title">Owner</div>
    </div>
    <div class="rule"></div>

    <ul class="contacts">
      <li>
        <svg viewBox="0 0 24 24" aria-hidden="true"><rect width="24" height="24" rx="4" fill="var(--brand-gold)"/><path d="M5 10c0-3 14-3 14 0v1h-3v-1.5h-8V11H5z M7 12h10l1 6H6z" fill="#fff"/></svg>
        555-014-2290
      </li>
      <li>
        <svg viewBox="0 0 24 24" aria-hidden="true"><rect width="24" height="24" rx="4" fill="var(--brand-gold)"/><rect x="8" y="4" width="8" height="16" rx="1.5" fill="#fff"/><rect x="9.5" y="6" width="5" height="5" fill="var(--brand-gold)"/></svg>
        +1 555-014-2291
      </li>
      <li>
        <svg viewBox="0 0 24 24" aria-hidden="true"><rect width="24" height="24" rx="4" fill="var(--brand-gold)"/><rect x="4" y="7" width="16" height="11" fill="#fff"/><path d="M4 7l8 6 8-6M4 18l6-5M20 18l-6-5" stroke="var(--brand-gold)" stroke-width="1.2" fill="none"/></svg>
        info@hartwellsecure.com
      </li>
    </ul>

    <div class="address">
      PO Box 418 Elm Street<br>
      Suite 2, WA 98000 USA
      <span class="web">www.hartwellsecure.com</span>
    </div>
  </section>
</body>
</html>
```